Business Card Design for Occupational Medicine Start Up Company

We need to design a professional business card. We are a healthcare company providing occupational medicine services to blue collar industries. We are professional, efficient and high quality service providers.

Target Market(s)

Blue Collar Industry: Shipbuilding, Ports, Trucking Companies; The Executives and Safety Officers for these companies

Industry/Entity Type

Healthcare

Contact Information for Business Card

Logo, Name, Title, Email, Phone

Other font styles liked:
• Please match our Brand Guide

Requirements
Must have
• Our Company Colors and Logo

```html
<!DOCTYPE html>
<html lang="en">
<head>
<meta charset="utf-8">
<title>Harborline Health Business Card</title>
<link href="https://fonts.googleapis.com/css2?family=Montserrat:wght@400;700&family=Questrial&display=swap" rel="stylesheet">
<style>
  :root {
    --backdrop: #2b2b2d;
    --sky: #29a8e0;
    --sky-deep: #12a0da;
    --navy: #263a86;
    --amber: #f2b455;
    --paper: #ffffff;
    --ink-soft: #6b6b6b;
  }
  * { box-sizing: border-box; margin: 0; padding: 0; }
  html, body { width: 1200px; height: 1024px; overflow: hidden; }
  body {
    background: var(--backdrop);
    position: relative;
    font-family: "Questrial", sans-serif;
  }
  .card {
    position: absolute;
    left: 180px;
    width: 840px;
    height: 480px;
    box-shadow: 0 10px 30px rgba(0,0,0,.5);
    overflow: hidden;
  }
  .card-back { top: 20px; background: var(--sky); }
  .card-front { top: 524px; background: var(--paper); }

  .brand-motif-faint {
    position: absolute;
    left: 0;
    top: 0;
    width: 470px;
    height: 480px;
    background: linear-gradient(135deg, var(--sky-deep) 0%, rgba(18,160,218,.55) 60%, rgba(18,160,218,0) 100%);
  }
  .brand-motif {
    position: absolute;
    left: 90px;
    bottom: 0;
    width: 310px;
    height: 215px;
    background: linear-gradient(160deg, var(--amber) 0%, var(--navy) 45%, var(--sky) 100%);
    opacity: .9;
  }

  .wordmark {
    position: absolute;
    display: flex;
    align-items: center;
    gap: 14px;
    font-family: "Montserrat", sans-serif;
    font-weight: 700;
    letter-spacing: .04em;
    text-transform: uppercase;
  }
  .wordmark .dot { width: 30px; height: 30px; border-radius: 50%; }
  .card-back .wordmark { right: 70px; bottom: 80px; font-size: 34px; color: var(--paper); }
  .card-back .wordmark .dot { background: var(--paper); }
  .card-front .wordmark { right: 70px; top: 70px; font-size: 30px; color: var(--navy); }
  .card-front .wordmark .dot { background: var(--navy); }

  .holder { position: absolute; left: 70px; top: 185px; }
  .holder-name {
    font-family: "Montserrat", sans-serif;
    font-weight: 700;
    font-size: 40px;
    color: var(--navy);
    text-transform: uppercase;
    letter-spacing: .01em;
  }
  .holder-title { font-size: 20px; color: var(--ink-soft); margin-top: 4px; }

  .contacts {
    position: absolute;
    right: 70px;
    bottom: 70px;
    list-style: none;
    font-size: 20px;
    color: var(--ink-soft);
  }
  .contacts li { display: flex; align-items: center; gap: 12px; margin-top: 8px; }
  .contacts svg { width: 20px; height: 20px; flex: none; }
</style>
</head>
<body>
  <section class="card card-back">
    <div class="brand-motif-faint" role="img" aria-label="Large faint brand symbol decoration"></div>
    <div class="wordmark"><span class="dot"></span>Harborline Health</div>
  </section>

  <section class="card card-front">
    <div class="wordmark"><span class="dot"></span>Harborline Health</div>

    <div class="holder">
      <h1 class="holder-name">Dana Whitfield</h1>
      <p class="holder-title">Executive Manager</p>
    </div>

    <div class="brand-motif" role="img" aria-label="Large brand symbol decoration in amber, navy and sky blue"></div>

    <ul class="contacts">
      <li>
        <svg viewBox="0 0 20 20" aria-hidden="true"><circle cx="10" cy="10" r="10" fill="var(--amber)"/><path d="M7 5.5c.6-.3 1.1 0 1.4.6l.6 1.3c.2.5 0 .9-.4 1.2l-.5.3c.5 1.2 1.5 2.2 2.7 2.7l.3-.5c.3-.4.7-.6 1.2-.4l1.3.6c.6.3.9.8.6 1.4-.5 1-1.5 1.6-2.6 1.2-2.6-.9-4.6-2.9-5.5-5.5C5.4 7 6 6 7 5.5z" fill="#fff"/></svg>
        555-010-4477
      </li>
      <li>
        <svg viewBox="0 0 20 20" aria-hidden="true"><circle cx="10" cy="10" r="10" fill="var(--amber)"/><rect x="5" y="6.5" width="10" height="7" rx="1" fill="#fff"/><path d="M5.5 7l4.5 3.5L14.5 7" stroke="var(--amber)" stroke-width="1.2" fill="none"/></svg>
        info@harborlinehealth.com
      </li>
      <li>
        <svg viewBox="0 0 20 20" aria-hidden="true"><circle cx="10" cy="10" r="10" fill="var(--amber)"/><path d="M10 5l5 4.5h-1.5V15h-2.5v-3H9v3H6.5V9.5H5z" fill="#fff"/></svg>
        Your address, your city, box 88900
      </li>
    </ul>
  </section>
</body>
</html>
```